Business Card Design

We have recently seen two business cards that caught our attention and think the designs would work for us. We are an accounting firm that serves small businesses in a variety of industries. Attached are the two business card that inspired us along with very rough layouts. We would like to see a professional layout using our company information.

Industry/Entity Type

Accounting

Contact Information for Business Card

Company Name - Marlowe Thistle
Address - 4182 Orlanby Lane, Suite 610, Houston, TX 77093
713-555-0187 - Main
281-555-0342 - Fax

Team Member Names, emails and phone numbers (see attachment)

```html
<!DOCTYPE html>
<html lang="en">
<head>
<meta charset="utf-8">
<title>Marlowe Thistle – Business Card</title>
<link rel="stylesheet" href="https://fonts.googleapis.com/css2?family=Lato:wght@400;700;900&display=swap">
<style>
  :root {
    --backdrop: #e6e4e1;
    --card: #ffffff;
    --ink: #111111;
    --muted: #8c8c8c;
    --accent: #f07a1e;
    --mark: #b9b9b9;
  }
  * { box-sizing: border-box; margin: 0; padding: 0; }
  html, body {
    width: 1200px;
    height: 539px;
    overflow: hidden;
    background: var(--backdrop);
  }
  body { position: relative; font-family: "Lato", sans-serif; color: var(--ink); }

  .business-card {
    position: absolute;
    left: 200px;
    top: 41px;
    width: 800px;
    height: 457px;
    background: var(--card);
    box-shadow: 0 6px 22px rgba(0,0,0,0.18);
  }

  .divider {
    position: absolute;
    left: 336px;
    top: 0;
    width: 4px;
    height: 100%;
    background: var(--accent);
  }

  /* Left panel: brand */
  .brand-mark {
    position: absolute;
    left: 70px;
    top: 150px;
    display: flex;
    align-items: center;
    gap: 12px;
  }
  .brand-mark .brand-square {
    width: 22px;
    height: 22px;
    background: var(--mark);
  }
  .brand-mark .brand-name {
    font-weight: 700;
    font-size: 26px;
    color: var(--ink);
  }
  .company-name {
    position: absolute;
    left: 48px;
    top: 330px;
    font-weight: 900;
    font-size: 30px;
    letter-spacing: 0.5px;
    text-transform: uppercase;
    white-space: nowrap;
  }
  .company-address {
    position: absolute;
    left: 48px;
    top: 372px;
    width: 280px;
    font-size: 15px;
    line-height: 1.5;
  }

  /* Right panel: team member */
  .member {
    position: absolute;
    right: 58px;
    top: 30px;
    text-align: right;
  }
  .member-name {
    font-weight: 900;
    font-size: 17px;
    text-transform: uppercase;
    letter-spacing: 0.3px;
  }
  .member-title {
    font-size: 10px;
    color: var(--muted);
    text-transform: uppercase;
    letter-spacing: 1px;
    margin-top: 1px;
  }
  .member-rule {
    position: absolute;
    left: 448px;
    top: 66px;
    width: 292px;
    height: 3px;
    background: var(--accent);
  }
  .member-contacts {
    position: absolute;
    left: 462px;
    top: 76px;
    font-size: 13px;
    line-height: 1.55;
  }
  .contact-row { display: flex; align-items: center; gap: 14px; }
  .contact-item { display: inline-flex; align-items: center; gap: 5px; }
  .icon { width: 11px; height: 11px; fill: var(--ink); flex: none; }

  /* Right panel: company details */
  .details-heading {
    position: absolute;
    left: 360px;
    top: 256px;
    font-size: 18px;
  }
  .details-rule {
    position: absolute;
    left: 340px;
    top: 282px;
    width: 212px;
    height: 3px;
    background: var(--accent);
  }
  .details-list {
    position: absolute;
    left: 362px;
    top: 292px;
    font-size: 17px;
    line-height: 1.55;
  }
  .details-list .contact-item { gap: 12px; }
  .details-list .icon { width: 15px; height: 15px; }
</style>
</head>
<body>
  <article class="business-card">
    <div class="divider"></div>

    <div class="brand-mark">
      <span class="brand-square"></span>
      <span class="brand-name">Marlowe Thistle</span>
    </div>
    <h1 class="company-name">Marlowe Thistle</h1>
    <p class="company-address">4182 Orlanby Lane, Suite 610, Houston, TX 77093</p>

    <div class="member">
      <div class="member-name">Delphine Arrowood</div>
      <div class="member-title">Account Manager</div>
    </div>
    <div class="member-rule"></div>
    <div class="member-contacts">
      <div class="contact-row">
        <span class="contact-item">
          <svg class="icon" viewBox="0 0 12 12" aria-hidden="true"><path d="M3 0h6a1 1 0 0 1 1 1v10a1 1 0 0 1-1 1H3a1 1 0 0 1-1-1V1a1 1 0 0 1 1-1zm0 1.5v8h6v-8z"/></svg>
          832-555-0129
        </span>
        <span class="contact-item">
          <svg class="icon" viewBox="0 0 12 12" aria-hidden="true"><path d="M1 3.5C1 2 3 1.5 6 1.5S11 2 11 3.5V5H8.5V4h-5v1H1zM3 5.5h6l2 3.5V11H1V9z"/></svg>
          713-555-0187
        </span>
      </div>
      <div class="contact-row">
        <span class="contact-item">
          <svg class="icon" viewBox="0 0 12 12" aria-hidden="true"><path d="M0 2h12v1.2L6 7 0 3.2zM0 4.6l6 3.8 6-3.8V10H0z"/></svg>
          darrowood@marlowethistle.com
        </span>
      </div>
    </div>

    <div class="details-heading">Company Details</div>
    <div class="details-rule"></div>
    <div class="details-list">
      <div class="contact-row">
        <span class="contact-item">
          <svg class="icon" viewBox="0 0 12 12" aria-hidden="true"><path d="M1 3.5C1 2 3 1.5 6 1.5S11 2 11 3.5V5H8.5V4h-5v1H1zM3 5.5h6l2 3.5V11H1V9z"/></svg>
          713-555-0187
        </span>
      </div>
      <div class="contact-row">
        <span class="contact-item">
          <svg class="icon" viewBox="0 0 12 12" aria-hidden="true"><path d="M3 0h6v3H3zM1 4h10a1 1 0 0 1 1 1v4H9.5v3h-7V9H0V5a1 1 0 0 1 1-1zm2.5 4v3h5V8z"/></svg>
          281-555-0342
        </span>
      </div>
    </div>
  </article>
</body>
</html>
```